Business Cards - Brightpath Horizon

need to design unique business card for my mortgage business. I need to design credit card style business card for my business or any unique idea that you might have

Target Market(s)

Home Loan customers

Industry/Entity Type

Mortgage Brokerage

Contact Information for Business Card

please design credit card style or very unique style business card

Colors

Designer to choose colors to be used in the design.

Requirements
Must have
• Name
• position
• Phone number
• fax number
• email address
• website address
• social media address
• All above fields will be provided once design in finalised

```html
<!DOCTYPE html>
<html lang="en">
<head>
<meta charset="utf-8">
<title>Brightpath Horizon – Business Cards</title>
<link href="https://fonts.googleapis.com/css2?family=Libre+Baskerville:ital@0;1&family=Work+Sans:wght@300;400&display=swap" rel="stylesheet">
<style>
  :root {
    --backdrop: #1b1b1b;
    --orange: #f58b22;
    --white: #ffffff;
    --sky: #2aa5de;
    --navy: #334ea1;
    --ink: #333333;
  }
  * { margin: 0; padding: 0; box-sizing: border-box; }
  html, body { width: 1200px; height: 897px; overflow: hidden; }
  body { background: var(--backdrop); position: relative; font-family: "Work Sans", sans-serif; }

  .card {
    position: absolute;
    left: 303px;
    width: 594px;
    height: 338px;
    overflow: hidden;
  }
  .card--front { top: 92px; background: var(--white); }
  .card--back  { top: 469px; background: var(--orange); }

  .holder-name {
    position: absolute; left: 25px; top: 20px;
    font-family: "Libre Baskerville", serif;
    font-size: 23px; font-weight: 400; letter-spacing: 1px;
    color: var(--sky);
  }
  .holder-role {
    position: absolute; left: 25px; top: 56px;
    font-size: 13px; letter-spacing: 0.6px; color: var(--ink);
  }

  .rooftop-art {
    position: absolute; left: 0; top: 78px;
    width: 594px; height: 134px;
    background: linear-gradient(100deg, var(--navy) 0%, var(--navy) 45%, #8a6f7a 62%, var(--orange) 100%);
  }

  .contact-band {
    position: absolute; left: 0; top: 212px;
    width: 594px; height: 126px;
    background: var(--orange);
    color: var(--white);
    font-weight: 300; font-size: 13.5px;
  }
  .contact-list { position: absolute; left: 24px; top: 46px; list-style: none; }
  .contact-list li { display: flex; align-items: center; height: 17px; }
  .contact-list svg { width: 8px; height: 8px; margin-right: 9px; }
  .address {
    position: absolute; right: 26px; top: 46px;
    text-align: right; line-height: 17px; font-style: normal;
  }

  .brand {
    position: absolute; left: 0; right: 0; top: 142px;
    text-align: center; color: var(--white);
  }
  .brand-name {
    font-family: "Libre Baskerville", serif;
    font-size: 30px; letter-spacing: 2px; text-transform: uppercase;
  }
  .brand-mark {
    display: inline-block; width: 14px; height: 14px;
    background: var(--white); margin-right: 12px; vertical-align: 4px;
  }
  .tagline {
    margin-top: 14px;
    font-family: "Libre Baskerville", serif; font-style: italic;
    font-size: 15px; letter-spacing: 0.5px;
  }
  .back-web {
    position: absolute; left: 0; right: 0; top: 297px;
    text-align: center; color: var(--white);
    font-size: 13px; letter-spacing: 2.4px; font-weight: 400;
  }
</style>
</head>
<body>
  <section class="card card--front">
    <h1 class="holder-name">DANIEL HART</h1>
    <p class="holder-role">Founder</p>
    <div class="rooftop-art" role="img" aria-label="Illustration of blue and orange house rooftops along a street"></div>
    <div class="contact-band">
      <ul class="contact-list">
        <li>
          <svg viewBox="0 0 10 10"><path d="M2 1 L4 1 L4.5 3.5 L3.3 4.3 Q4.5 6.5 5.7 6.7 L6.5 5.5 L9 6 L9 8 Q8.5 9 7.5 9 Q1 8 1 2 Q1 1 2 1Z" fill="#2aa5de"/></svg>
          555-210-4470
        </li>
        <li>
          <svg viewBox="0 0 10 10"><rect x="0.8" y="2" width="8.4" height="6" fill="none" stroke="#2aa5de" stroke-width="1.2"/><path d="M1 2.3 L5 5.5 L9 2.3" fill="none" stroke="#2aa5de" stroke-width="1.1"/></svg>
          hello@brightpathhorizon.com
        </li>
        <li>
          <svg viewBox="0 0 10 10"><circle cx="5" cy="5" r="4" fill="none" stroke="#2aa5de" stroke-width="1.2"/><path d="M1 5 H9 M5 1 Q2.5 5 5 9 M5 1 Q7.5 5 5 9" fill="none" stroke="#2aa5de" stroke-width="0.9"/></svg>
          www.brightpathhorizon.com
        </li>
      </ul>
      <address class="address">480 Harbor Lane<br>Seaview, FL 33000</address>
    </div>
  </section>

  <section class="card card--back">
    <div class="brand">
      <div class="brand-name"><span class="brand-mark"></span>Brightpath Horizon</div>
      <p class="tagline">Clear keys, Open doors</p>
    </div>
    <p class="back-web">www.yourwebsite.com</p>
  </section>
</body>
</html>
```